Simple Logo Design for Semi-Clear Plastic Frosted Card stock

Create a business card on frosted plastic. compliment existing logo elements with a tree trunk, roots, or seed at the lower half and the full logo both on the front.

Contact information will go on a solid portion of the back of this design since this card stock is semi-transparent.

It is important to consider this plastic card stock medium in your design. I found helpful tips and guides listed at vellaprint-sample.net: be careful to understand ink printed on plastic cards cannot have too much of a consistent print area or risks peeling and fine lines can easily scratch off.
Updates

2" x 3.5" 20PT Clear Plastic Business cards with Round corners Please get info or templates here: https://www.vellaprint-sample.net/product-detail/2-x-35-20pt-clear-plastic-business-cards-with-round-corners

Target Market(s)

Not for profit- religion

Industry/Entity Type

Business

Must include complementary elements to the existing logo

Font styles to use
Decorative

Colors
000000

Requirements
Must have
• Elements of community, nature and oneness. Such as: seed, roots, tree trunk, etc.
• Three lines of space on the back for Name, Title, Phone Number.
Nice to have
• I like a light use of decorative elements
Should not have
• No eyes, from faces or animals.

```html
<!DOCTYPE html>
<html lang="en">
<head>
<meta charset="utf-8">
<title>Meadowpath Business Card</title>
<link rel="stylesheet" href="https://fonts.googleapis.com/css2?family=Source+Sans+3:wght@400;600&display=swap">
<style>
  :root {
    --backdrop: #e9ebea;
    --frost: #f6f7f7;
    --teal: #226e6b;
    --leaf: #3c9a3e;
    --ink: #333333;
    --paper: #ffffff;
  }
  * { margin: 0; padding: 0; box-sizing: border-box; }
  html, body {
    width: 1200px;
    height: 900px;
    overflow: hidden;
    background: var(--backdrop);
    font-family: "Source Sans 3", sans-serif;
  }
  .card {
    position: absolute;
    left: 275px;
    top: 250px;
    width: 650px;
    height: 400px;
    border-radius: 22px;
    background: var(--frost);
    overflow: hidden;
    box-shadow: 0 2px 10px rgba(0, 0, 0, 0.08);
  }
  .card-holder {
    position: absolute;
    top: 22px;
    width: 100%;
    text-align: center;
  }
  .holder-name {
    font-weight: 600;
    font-size: 25px;
    letter-spacing: 0.5px;
    line-height: 1.1;
    color: var(--teal);
  }
  .holder-name .surname { color: var(--leaf); }
  .holder-title {
    font-size: 18px;
    color: var(--ink);
    line-height: 1.3;
  }
  .brand {
    position: absolute;
    top: 168px;
    left: 0;
    width: 100%;
    display: flex;
    justify-content: center;
    align-items: center;
    gap: 14px;
  }
  .brand-dot {
    width: 26px;
    height: 26px;
    border-radius: 50%;
    background: var(--leaf);
  }
  .brand-name {
    font-size: 42px;
    font-weight: 400;
    letter-spacing: 2px;
    color: var(--teal);
  }
  .accent-line {
    position: absolute;
    left: 0;
    top: 311px;
    width: 100%;
    height: 5px;
    background: var(--leaf);
  }
  .contact-band {
    position: absolute;
    left: 0;
    top: 324px;
    width: 100%;
    height: 76px;
    background: var(--teal);
    display: flex;
    justify-content: center;
    align-items: center;
    gap: 6px;
    color: var(--paper);
    font-size: 18px;
  }
  .phone-icon { width: 15px; height: 13px; }
</style>
</head>
<body>
  <div class="card">
    <div class="card-holder">
      <div class="holder-name">DANIEL <span class="surname">REYES</span></div>
      <div class="holder-title">Managing Direcator</div>
    </div>

    <div class="brand">
      <span class="brand-dot"></span>
      <span class="brand-name">MEADOWPATH</span>
    </div>

    <div class="accent-line"></div>

    <div class="contact-band">
      <svg class="phone-icon" viewBox="0 0 15 13" aria-hidden="true">
        <path d="M1 4 Q7.5 -1 14 4 L12 6 L10 4.5 L10 3.5 Q7.5 2.5 5 3.5 L5 4.5 L3 6 Z" fill="#ffffff"/>
        <rect x="3" y="6.5" width="9" height="6" rx="1" fill="#ffffff"/>
      </svg>
      <span class="phone-number">823-555-0147</span>
    </div>
  </div>
</body>
</html>
```